Brochure/flyer for our trip to Paris

Our company is taking us all on a summer trip to Paris. We have some key information that we need to tell everybody about the trip. We think a nicely designed brochure or flyer, which uses our brand colours and guidelines, would be something nice to keep during the trip and as a memento afterwards.

We are looking for a brochure or a flyer which contains all the info in the attached document.

This needs to happen really fast as we actually go to Paris on the 13th August. We also need time to print it!

We can provide a library of icons. All images in the document can be changed. you don't have to use the images in the document.

Target Market(s)

People in our company. They are fun and as this is for a party the flyer needs to feel uplifting.

Industry/Entity Type

Health

Font styles to use
Other font styles liked:
• Nexa - please see attached font.

Requirements
Must have
• Designers must stick to our brand guideline, font and the colours we use.
• Please also see attached content for the flyer.
• This website shows our style - https://www.lorventi.com/fr
Should not have
• Please don't make it too tacky or too much about French things. It can be a bit playful but not too much.

```html
<!DOCTYPE html>
<html lang="en">
<head>
<meta charset="utf-8">
<title>Paris Trip Brochure – Inside</title>
<link rel="stylesheet" href="https://fonts.googleapis.com/css2?family=Montserrat:wght@300;400;600;700&display=swap">
<style>
  :root {
    --page-bg: #ececec;
    --paper: #ffffff;
    --brand-blue: #1ba3e2;
    --ink: #1d1d1d;
    --ink-soft: #3a3a3a;
    --sky-top: #ffffff;
    --sky-mid: #eef0f1;
    --haze: #d9d8d3;
    --stone: #a79c8d;
    --roof: #8a7f72;
  }
  * { box-sizing: border-box; margin: 0; padding: 0; }
  html, body { width: 1200px; height: 1000px; overflow: hidden; }
  body {
    background: var(--page-bg);
    font-family: "Montserrat", sans-serif;
    color: var(--ink);
    position: relative;
  }
  .brochure {
    position: absolute;
    left: 178px; top: 168px;
    width: 853px; height: 662px;
    background: var(--paper);
    overflow: hidden;
  }
  .brochure-photo {
    position: absolute; inset: 0;
    background: linear-gradient(180deg,
      var(--sky-top) 0%, var(--sky-top) 55%,
      var(--sky-mid) 72%, var(--haze) 86%, var(--stone) 94%, var(--roof) 100%);
  }
  .panel {
    position: absolute; top: 10px;
    font-size: 11.6px; line-height: 16px; font-weight: 400;
    color: var(--ink-soft);
  }
  .panel-metro { left: 15px; width: 262px; }
  .panel-itinerary { left: 298px; width: 264px; }
  .panel-phrases { left: 580px; width: 258px; }

  .heading { font-size: 25px; line-height: 28px; font-weight: 300; color: var(--ink); letter-spacing: .5px; }
  .heading .accent { color: var(--brand-blue); font-weight: 700; }
  .heading .strong { font-weight: 700; }
  .heading-block { display: block; }

  .metro-copy p { text-align: justify; margin-bottom: 2px; }
  .metro-copy { margin-top: 8px; }
  .tips { margin-top: 12px; padding-left: 3px; }
  .tips .heading { margin-bottom: 8px; }
  .tips p { font-size: 11px; line-height: 15px; margin-bottom: 6px; }

  .day-title { font-weight: 700; color: var(--ink); margin: 14px 0 5px; font-size: 11.6px; }
  .day-title:first-of-type { margin-top: 16px; }
  .day-body { padding-left: 11px; }
  .day-body p { margin-bottom: 0; }
  .day-body .gap { margin-top: 3px; }

  .emergency { margin-top: 26px; }
  .contacts { list-style: none; margin-top: 14px; padding-left: 13px; font-size: 12px; line-height: 22px; }
  .contacts li { display: flex; }
  .contacts .name { width: 64px; }

  .phrases-intro { font-weight: 700; color: var(--ink); margin: 18px 0 13px; }
  .phrase-list { list-style: none; padding-left: 6px; }
  .phrase-list li { font-size: 11px; line-height: 15px; margin-bottom: 6.4px; text-align: justify; }
  .phrase-list b { font-size: 11.8px; font-weight: 700; color: var(--ink); }
</style>
</head>
<body>
  <section class="brochure" aria-label="Paris trip brochure, inside spread">
    <div class="brochure-photo" role="img" aria-label="Photograph: stone gargoyle in the foreground overlooking the Paris skyline with the Eiffel Tower in a hazy sky"></div>

    <article class="panel panel-metro">
      <h2 class="heading"><span class="accent heading-block">HOW TO</span><span class="heading-block">USE THE METRO:</span></h2>
      <div class="metro-copy">
        <p>You have each been given 3 Metro tickets to help you on your way. Although you may need additional tickets depending on what your plans are in your free time.</p>
        <p>They are €4 for a single journey. Once you're in the Metro station, how to use the tickets is pretty self explanatory.</p>
        <p>Tip from Elodie the tickets have a magnetic strip so try and keep them away from bank cards etc. If you find that any of your tickets do not work, you can ask at the kiosk for a replacement.</p>
      </div>
      <div class="tips">
        <h2 class="heading"><span class="accent">TOP</span> TIPS:</h2>
        <p>The best way to find your way around is to use Route Hopper or alternatively:</p>
        <p>http://www.metrolien.fr/itineraires/en/plan<br>/rechercheavancee</p>
      </div>
    </article>

    <article class="panel panel-itinerary">
      <h2 class="heading"><span class="accent">ITINERARY</span></h2>
      <h3 class="day-title">13th August</h3>
      <div class="day-body"><p>Arrive in Paris at 11:17am local time. Drop bags to hotel, grab lunch and enjoy our 1 hour River Seine Tour.</p></div>
      <h3 class="day-title">Free time2:</h3>
      <div class="day-body">
        <p>3:07pm (you will need to go and officially check in at the hotel and get ready for the evening within this time)</p>
        <p>7pm: Drinks and dinner at.......</p>
        <p>Late night drinks at........</p>
      </div>
      <h3 class="day-title">The next day.....</h3>
      <div class="day-body">
        <p>Check out between 9:10am at the latest and enjoy some breakfast at the hotel. Casual walk up to Gare du nord, enjoying Paris that little bit more before we leave.</p>
        <p class="gap">Everyone must be at Gare du nord by 2pm at the very latest to check in!</p>
      </div>
      <div class="emergency">
        <h2 class="heading"><span class="strong heading-block">EMERGENCY</span><span class="heading-block">INTERNAL CONTACTS:</span></h2>
        <ul class="contacts">
          <li><span class="name">Maren</span><span>07700900114</span></li>
          <li><span class="name">Tobias</span><span>07700900287</span></li>
          <li><span class="name">Callum</span><span>07700900352</span></li>
          <li><span class="name">Noura</span><span>07700900469</span></li>
        </ul>
      </div>
    </article>

    <article class="panel panel-phrases">
      <h2 class="heading"><span class="accent">Some</span> Mustknow</h2>
      <p class="phrases-intro">French Phrases for Savvy Travellers:</p>
      <ol class="phrase-list">
        <li><b>1. Bonjour.</b> (Hello)</li>
        <li><b>2. Oui / Non</b> (Yes / No)</li>
        <li><b>3. Parlezvous anglais?</b> (Do you speak English?)</li>
        <li><b>4. Où est le métro?</b> (Where is the Metro?)</li>
        <li><b>5. Où est…?</b> (Where is…?)</li>
        <li><b>6. Où est le guichet ?</b>(Where is the ticket window?)</li>
        <li><b>7. Combien ça coûte?</b> (How much does it cost?)</li>
        <li><b>8. Merci!</b> (Thank you!)</li>
        <li><b>9. Bonsoir</b> (Hello/good evening)</li>
        <li><b>10. Au Revoir</b> (Goodbye)</li>
        <li><b>11. Puisje me connecter à Internet?</b> (Can I get on the internet?)</li>
        <li><b>12. Je ne comprends pas.</b> (I don't understand)</li>
        <li><b>13. Je ne sais pas.</b> (I don't know)</li>
        <li><b>14. Estce que vous pouvez l'écrire?</b> (Could you please write it down?)</li>
        <li><b>15. Pouvezvous m'aider, s'il vous plaît?</b> (Can you help me please?)</li>
      </ol>
    </article>
  </section>
</body>
</html>
```